Flalzflyer-Design (Folder)
Da für uns neben einem guten Design ein angenehmer und konstruktiver Dialog sowie Verlässlichkeit von hoher Bedeutung ist, sind wir sehr froh auf dieser Plattform auf "brightloom" gestoßen zu sein. Wir sagen ganz herzlich DANKE!!
Zielgruppe
Zielgruppe im Bereich der Vermietung sind Alleinreisende oder als Paar verreisende Natur- und Nordsee verbundene Feriengäste (ü30) mit dem Urlaubsziel 'Sylt', welche eine persönlich und mit besonderem Schick eingerichtet Ferienwohnung/Ferienapartment in zentraler Lage in Westerland suchen und die es als positiven bzw. interessanten Aspekt sehen, dass die Ferienwohnungen direkt von uns Insulaner angeboten werden und wir als Sylter Familie ebenfalls Vor-Ort mit dem Urlaubern unter dem selben Dach leben (wenn auch nicht in der derselben Wohnung ;) ), ganz gemäß unserem Slogan 'Nordseeurlaub unter einem Dach mit Insulanern'
Aufgabenstellung
Es soll ein Falzflyer (Folder) mit Wickelfalz (siehe ggf. https://www.druckwerk-nord.de/werbemittel/folder.html) designed werden (4/4-farbig Euroskala). Bestehend aus einem Papier Format DIN A4 mit zwei Falzen, sodass sich bei Berücksichtigung von Vor- u. Rückseite 6 Seiten ergeben. Die wesentlichen Texte/Inhalte/Informationen, finden sich hier: https://www.quartiersuche-online.de/481926/ . Neben dem Ferienapartment 'Kompass' w ird von uns die Ferienwohnung 'Wadlen' (friesisch für Seestern) angeboten, ebenfalls im Morgenlicht Sylt HOUSE (EST. 2017).
Preisangaben können unberücksichtigt beliben, da sie dem Folder später über eine gesondere Einlage beigelegt werden sollen.
Im Rahmen des Dateiupload bei entwurfsmarkt werden nur einige der möglichen Fotos bereitgestellt. Sie sollen als Auswahlmöglichkeit dienen. Welche der Fotos Verwendung finden oder nach weiteren nachgefragt wird, soll in Abhängigkeit mit dem Gesamtdesign stehen und zunächst von Ihnen entschieden werden, um ein möglichst ansprechenden und harmonischen Folder kreieren zu können.

```html
<!DOCTYPE html>
<html lang="de">
<head>
<meta charset="utf-8">
<title>Morgenlicht Sylt HOUSE – Folder</title>
<link href="https://fonts.googleapis.com/css2?family=Arimo:wght@400;700&family=Caveat:wght@400&family=Lato:wght@400;700&display=swap" rel="stylesheet">
<style>
:root{
  --blue:#3f9ccd;
  --script:#4a9fd0;
  --ink:#333;
  --ink-soft:#555;
  --rule:#e4e4e4;
  --paper:#fff;
}
*{margin:0;padding:0;box-sizing:border-box}
html,body{width:840px;height:1200px;overflow:hidden;background:var(--paper)}
.folder{position:relative;width:840px;height:1200px;overflow:hidden;color:var(--ink);font-family:"Lato",sans-serif}
.abs{position:absolute}
.photo{position:absolute}
.script{position:absolute;font-family:"Caveat",cursive;font-weight:400;color:var(--script);font-size:26px;line-height:1;white-space:nowrap}
.fold-rule{position:absolute;left:0;top:600px;width:840px;height:1px;background:var(--rule)}
.body-sans{font-family:"Arimo",sans-serif;font-size:8.6px;line-height:12.8px;color:var(--ink)}
.visit-title{font-size:15px;line-height:19px;color:var(--ink-soft);font-weight:700;letter-spacing:.2px}
.visit-title span{font-weight:400}
.visit-text{font-size:8.6px;line-height:13.7px;color:var(--ink-soft)}
.visit-text p{margin-bottom:6px}
.dash{position:absolute;left:290px;top:451px;width:251px;border-top:1.2px dashed var(--blue)}
.contact{font-size:8.8px;line-height:12.9px;color:var(--ink-soft)}
.contact b{color:var(--ink)}
.house-name{text-align:center;color:var(--ink-soft)}
.house-name .name{font-size:13px;font-weight:700}
.house-name .est{font-size:10.5px}
.welcome{text-align:center;font-size:17px;line-height:19px;color:var(--ink-soft);font-weight:400}
.welcome b{font-weight:700}
.amen{position:absolute;display:flex;justify-content:space-between}
.amen .item{width:52px;text-align:center;font-family:"Arimo",sans-serif;font-size:6.4px;line-height:8.6px;color:var(--ink-soft)}
.amen svg{display:block;margin:0 auto 4px}
.sea-label{position:absolute;left:421px;top:228px;width:118px;font-family:"Caveat",cursive;font-size:9px;line-height:1;color:#fff;white-space:nowrap}
.tagline{left:569px;top:420px;width:257px;text-align:center;font-size:25px}
</style>
</head>
<body>
<div class="folder">

  <!-- Top: inner cover panels -->
  <div class="script" style="left:50px;top:38px;font-size:27px;">Wir freuen uns auf Sie!</div>
  <div class="photo" role="img" aria-label="Dekoration mit Schaf-Figur vor heller Schrift-Tapete" style="left:14px;top:82px;width:82px;height:148px;background:linear-gradient(160deg,#c9c6bd,#a9a79f 60%,#ece9e2)"></div>
  <div class="photo" role="img" aria-label="Holzregal mit Sylt-Schriftzug und Vogel-Figur" style="left:98px;top:82px;width:164px;height:148px;background:linear-gradient(150deg,#8c8678,#6d5a44 55%,#7a2f2a)"></div>
  <div class="photo" role="img" aria-label="Straßenkarte der Region mit Standortmarkierung" style="left:14px;top:233px;width:248px;height:201px;background:linear-gradient(135deg,#e9efe4,#f3f1ec 55%,#e6ebf0)"></div>
  <div class="photo" role="img" aria-label="Pantryküche mit gelber Wand und Strandgemälde" style="left:14px;top:438px;width:154px;height:147px;background:linear-gradient(170deg,#8fb0c4,#c9b12a 45%,#b48f5e 80%,#8d8d8d)"></div>
  <div class="photo" role="img" aria-label="Holzherz an einem Haken an heller Holzwand" style="left:171px;top:438px;width:91px;height:147px;background:linear-gradient(90deg,#bdb5aa,#d9d3ca 50%,#aea499)"></div>

  <div class="photo" role="img" aria-label="Hausansicht mit Klinkerfassade und Garten" style="left:290px;top:16px;width:124px;height:228px;background:linear-gradient(175deg,#3d79c2,#e8e8e6 30%,#c49a55 55%,#4d6a2e 78%,#a4563f)"></div>
  <div class="photo" role="img" aria-label="Hortensien und Kaffeetassen auf der Terrasse" style="left:417px;top:16px;width:124px;height:112px;background:linear-gradient(170deg,#5b6db0,#7d83c7 40%,#3f5a2c 65%,#d9d9e2)"></div>
  <div class="photo" role="img" aria-label="Badende in der Nordsee unter bewölktem Himmel" style="left:417px;top:130px;width:124px;height:114px;background:linear-gradient(180deg,#dfe3e5,#a7b0b2 50%,#6b767a)"></div>
  <div class="sea-label">unsere Meerwasser-Schwimmanlage</div>

  <div class="abs visit-title" style="left:290px;top:259px;">BESUCHEN SIE UNS<br><span>AUF SYLT.</span></div>
  <div class="abs visit-text" style="left:290px;top:305px;width:252px;">
    <p>Das Morgenlicht Sylt House (est. 2017) ist in Nachbarschaft des denkmalgeschützten Westerländer Polizeigebäudes (ehem. Amtsgericht) gelegen. Die vorteilhafte Lage ist damit zentral aber ruhig in 2. Reihe in Alt-Westerland.</p>
    <p>Der Bahnhof ist ca. 4-5 Gehminuten, die Fußgängerzone/Fried-richstr. mit div. Einkaufsmöglichkeiten und Restaurants/Cafés ca. 7 Min. und der Strand/die Kurpromenade ca. 12 Min. entfernt. Auch das Schwimmbad Inselbad Welle, das Inselvital Center (Well-ness) o. die Spielbank sind nah.</p>
  </div>
  <div class="dash"></div>
  <div class="abs contact" style="left:290px;top:459px;width:252px;">
    Familie Morgenlicht<br>
    <b>Morgenlicht Sylt HOUSE (EST. 2017)</b><br>
    Dünenweg 14b, Westerland<br><br>
    <b>Wir sind für Sie da</b> · &nbsp;Mo - So &nbsp;&nbsp;9.00 - 21.00<br>
    Telefon:+49 (0)4651 - 300 5127 · Mobil: +49 (0)170 - 555 0192<br>
    eMail: sylt@morgenlicht-haus.de<br>
    Belegungskalender: belegung.morgenlicht-haus.de<br>
    Mehr Fotos + Preise finden Sie auf: quartiersuche-online.de<br>
    =&gt; Wohin: Morgenlicht Sylt
  </div>

  <div class="photo" role="img" aria-label="Strand mit Strandkörben, Rettungsturm und Dünengras" style="left:569px;top:16px;width:257px;height:377px;background:linear-gradient(180deg,#3d86d0,#b7d2ec 30%,#2d5c86 45%,#e6dccb 60%,#2a4a8a 72%,#9b7e64)"></div>
  <div class="script tagline">Nordseeurlaub bei Insulanern</div>
  <div class="abs house-name" style="left:569px;top:455px;width:257px;">
    <div class="name">Morgenlicht Sylt HOUSE</div>
    <div class="est">(EST. 2017)</div>
  </div>
  <div class="abs welcome" style="left:569px;top:513px;width:257px;">HERZLICH WILLKOMMEN<br><b>BEI FAMILIE MORGENLICHT!</b></div>

  <div class="fold-rule"></div>

  <!-- Bottom left: apartment Kompass -->
  <div class="script" style="left:14px;top:624px;">Ferienapartment 'Kompass'</div>
  <div class="photo" role="img" aria-label="Schlafzimmer mit Einzelbett und Nachttisch" style="left:14px;top:660px;width:127px;height:123px;background:linear-gradient(160deg,#cfc9c0,#8a6d52 55%,#efece6)"></div>
  <div class="photo" role="img" aria-label="Wohnbereich mit Sofa und Beistelltisch" style="left:145px;top:660px;width:126px;height:123px;background:linear-gradient(160deg,#d9d6d0,#eeece8 45%,#3f3d3d 75%,#8da7b5)"></div>
  <div class="abs body-sans" style="left:14px;top:791px;width:258px;">Das Apartment ist seniorengerecht, ebenerdig, kurze Wege, An-sprechpartner im Haus, Bahnhof Westerland fussläufig 5 Min.</div>
  <div class="photo" role="img" aria-label="Grundriss des Apartments mit Nordpfeil und Außenbereich" style="left:14px;top:826px;width:248px;height:114px;background:linear-gradient(180deg,#f2f2ec,#e8eef4 60%,#f6f4e4)"></div>
  <div class="abs body-sans" style="left:14px;top:958px;width:260px;">
    <b>Wer Meer hat, braucht weniger, sagt man.</b><br>
    Die Zimmer persönlich und mit Geschick gestaltet, zeitgemäße Wohneinrichtung, modernes ebenerdiges Duschbad, hochwertige Pantryküche, Smart-TV, Wlan, ansprechendes und vollständiges Geschirr, Außenbereich sowie der persönlichen Nähe zu uns Insulanern.<br><br>
    Das App. eignet sich für einen längeren Urlaub besonders für 1 Person. Es steht ein Einzelbett im kl. Schlafzimmer zur Verfü-gung. Für einen Aufenthalt von einigen Tagen haben 2 Pers. ebenfalls eine passend schöne Unterkunft (Schlafmöglichkeit auf komfortablen Schlafsofa mit Lattenrost).
  </div>
  <div class="amen" style="left:10px;top:1124px;width:258px;">
    <div class="item"><svg width="38" height="38" viewBox="0 0 38 38"><circle cx="19" cy="19" r="17" fill="none" stroke="var(--blue)" stroke-width="2"/><path d="M10 16a13 13 0 0 1 18 0M13 19.5a8.5 8.5 0 0 1 12 0M16 23a4 4 0 0 1 6 0" fill="none" stroke="var(--blue)" stroke-width="2.2" stroke-linecap="round"/><circle cx="19" cy="26.5" r="1.6" fill="var(--blue)"/></svg>kostenloses<br>WLAN</div>
    <div class="item"><svg width="38" height="38" viewBox="0 0 38 38"><circle cx="19" cy="19" r="17" fill="none" stroke="var(--blue)" stroke-width="2"/><rect x="9" y="20" width="18" height="4" fill="var(--blue)"/><rect x="28" y="20" width="2" height="4" fill="var(--blue)"/><path d="M26 12c2 2 0 4 2 6" fill="none" stroke="var(--blue)" stroke-width="1.5"/><path d="M9 11l20 17" stroke="var(--blue)" stroke-width="2.5"/></svg>Nichtraucher<br>Wohnung</div>
    <div class="item"><svg width="38" height="38" viewBox="0 0 38 38"><circle cx="19" cy="19" r="17" fill="none" stroke="var(--blue)" stroke-width="2"/><path d="M11 27V14q8-6 16 0v13z" fill="none" stroke="var(--blue)" stroke-width="2"/><path d="M14 15v10M17 13v12M20 13v12M23 13v12" stroke="var(--blue)" stroke-width="1.2"/></svg>Strandkorb<br>vorhanden</div>
    <div class="item"><svg width="38" height="38" viewBox="0 0 38 38"><circle cx="19" cy="19" r="17" fill="none" stroke="var(--blue)" stroke-width="2"/><rect x="11" y="10" width="16" height="18" rx="1.5" fill="none" stroke="var(--blue)" stroke-width="2"/><path d="M11 14h16" stroke="var(--blue)" stroke-width="1.5"/><circle cx="19" cy="21" r="3.5" fill="none" stroke="var(--blue)" stroke-width="1.5"/></svg>Geschirrspüler<br>vorhanden</div>
    <div class="item"><svg width="38" height="38" viewBox="0 0 38 38"><circle cx="19" cy="19" r="17" fill="none" stroke="var(--blue)" stroke-width="2"/><path d="M10 13v14M10 24h18v3M16 19h12v5" fill="none" stroke="var(--blue)" stroke-width="2"/><circle cx="13" cy="20" r="2" fill="var(--blue)"/></svg>Bettwäsche &amp;<br>Handtücher</div>
  </div>

  <!-- Bottom middle: about us -->
  <div class="script" style="left:298px;top:624px;">Wer sind wir</div>
  <div class="abs body-sans" style="left:298px;top:663px;width:252px;">Wir sind eine 3-köpfige Familie, die ganzjährig im Morgenlicht Sylt HOUSE (Est. 2017) lebt und auf Wunsch gerne helfend mit Urlaubstipps und Klönschnack zur Verfügung steht. Unsere Tochter geht in Westerland zur Schule.</div>
  <div class="script" style="left:298px;top:727px;">Warum sind wir Gastgeber</div>
  <div class="abs body-sans" style="left:298px;top:766px;width:252px;">Weil wir als offene Menschen neue Begegnungen schätzen und so unseren Traum - ganzjährig auf Sylt zu leben - in die Tat umsetzen können.</div>
  <div class="photo" role="img" aria-label="In den Sand geschriebene Buchstaben" style="left:298px;top:810px;width:82px;height:123px;background:linear-gradient(160deg,#b9b7b3,#9e9b96 50%,#c6c3be)"></div>
  <div class="photo" role="img" aria-label="Weiter Strand mit Dünen und Meer" style="left:384px;top:810px;width:166px;height:123px;background:linear-gradient(180deg,#3a7fd2,#9fc3ea 45%,#4d7ea3 55%,#cdbfa4 70%,#7d8a4a)"></div>
  <div class="photo" role="img" aria-label="Spaziergänger am Strand unter Wolkenhimmel" style="left:298px;top:936px;width:150px;height:100px;background:linear-gradient(180deg,#4c86cc,#e9eef3 45%,#9aa4a9 70%,#d6cfc2)"></div>
  <div class="photo" role="img" aria-label="Sonnenuntergang über der Nordsee" style="left:451px;top:936px;width:99px;height:100px;background:linear-gradient(180deg,#2b3b52,#e77a2a 52%,#4a3a2a 62%,#1f1a15)"></div>
  <div class="script" style="left:298px;top:1057px;">Unser Service für Sie</div>
  <div class="abs body-sans" style="left:298px;top:1094px;width:252px;">
    Kostenloser Hol-/Bringservice Bahnhof Westerland nach Absprache möglich.<br><br>
    Das Wäschepaket beinhaltet: Bettwäsche, Laken, Handtuch (2x), Duschtuch, Badvorleger, Geschirrtuch.<br><br>
    Endreinigung inklusive.
  </div>

  <!-- Bottom right: Wohnung Wadlen -->
  <div class="script" style="left:577px;top:624px;">Ferienwohnung 'Wadlen'</div>
  <div class="photo" role="img" aria-label="Schlafzimmer mit Doppelbett und bunter Tagesdecke" style="left:577px;top:660px;width:124px;height:123px;background:linear-gradient(170deg,#6d625a,#e9e6e0 45%,#d9495c 75%,#efece8)"></div>
  <div class="photo" role="img" aria-label="Duschbad mit Holzwand und Blumen" style="left:704px;top:660px;width:122px;height:123px;background:linear-gradient(160deg,#4b3b30,#5d4a3c 50%,#e8e6e2 70%,#4e7a3e)"></div>
  <div class="abs body-sans" style="left:577px;top:791px;width:252px;">Das Apartment ist seniorengerecht, ebenerdig, kurze Wege, Ansprechpartner im Haus, Bahnhof Westerland fussläufig.</div>
  <div class="photo" role="img" aria-label="Grundriss der Wohnung mit Nordpfeil und Außenbereich" style="left:577px;top:826px;width:249px;height:114px;background:linear-gradient(180deg,#f2f2ec,#e8eef4 60%,#f6f4e4)"></div>
  <div class="abs body-sans" style="left:577px;top:958px;width:252px;">
    <b>Wer Meer hat, braucht weniger, sagt man.</b><br>
    Die Zimmer persönlich und mit Geschick gestaltet, zeitgemäße Wohneinrichtung, modernes ebenerdiges Duschbad, hoch-wertige Pantryküche, Smart-TV, Wlan, ansprechendes und vollständiges Geschirr, Außenbereich sowie der persönlichen Nähe zu uns Insulanern.<br><br>
    Das App. eignet sich für einen längeren Urlaub besonders für 1 Person. Es steht ein Einzelbett im kl. Schlafzimmer zur Ver-fügung. Für einen Aufenthalt von einigen Tagen haben 2 Pers. ebenfalls eine passend schöne Unterkunft (Schlafmöglichkeit auf komfortablen Schlafsofa mit Lattenrost).
  </div>
  <div class="amen" style="left:573px;top:1118px;width:256px;">
    <div class="item"><svg width="38" height="38" viewBox="0 0 38 38"><circle cx="19" cy="19" r="17" fill="none" stroke="var(--blue)" stroke-width="2"/><path d="M10 16a13 13 0 0 1 18 0M13 19.5a8.5 8.5 0 0 1 12 0M16 23a4 4 0 0 1 6 0" fill="none" stroke="var(--blue)" stroke-width="2.2" stroke-linecap="round"/><circle cx="19" cy="26.5" r="1.6" fill="var(--blue)"/></svg>kostenloses<br>WLAN</div>
    <div class="item"><svg width="38" height="38" viewBox="0 0 38 38"><circle cx="19" cy="19" r="17" fill="none" stroke="var(--blue)" stroke-width="2"/><rect x="9" y="20" width="18" height="4" fill="var(--blue)"/><rect x="28" y="20" width="2" height="4" fill="var(--blue)"/><path d="M26 12c2 2 0 4 2 6" fill="none" stroke="var(--blue)" stroke-width="1.5"/><path d="M9 11l20 17" stroke="var(--blue)" stroke-width="2.5"/></svg>Nichtraucher<br>Wohnung</div>
    <div class="item"><svg width="38" height="38" viewBox="0 0 38 38"><circle cx="19" cy="19" r="17" fill="none" stroke="var(--blue)" stroke-width="2"/><rect x="10" y="11" width="18" height="12" rx="1.5" fill="none" stroke="var(--blue)" stroke-width="2"/><path d="M19 23v3M14 27h10" stroke="var(--blue)" stroke-width="2"/></svg>Smart TV<br>vorhanden</div>
    <div class="item"><svg width="38" height="38" viewBox="0 0 38 38"><circle cx="19" cy="19" r="17" fill="none" stroke="var(--blue)" stroke-width="2"/><rect x="11" y="10" width="16" height="18" rx="1.5" fill="none" stroke="var(--blue)" stroke-width="2"/><path d="M11 14h16" stroke="var(--blue)" stroke-width="1.5"/><circle cx="19" cy="21" r="3.5" fill="none" stroke="var(--blue)" stroke-width="1.5"/></svg>Geschirrspüler<br>vorhanden</div>
    <div class="item"><svg width="38" height="38" viewBox="0 0 38 38"><circle cx="19" cy="19" r="17" fill="none" stroke="var(--blue)" stroke-width="2"/><path d="M10 13v14M10 24h18v3M16 19h12v5" fill="none" stroke="var(--blue)" stroke-width="2"/><circle cx="13" cy="20" r="2" fill="var(--blue)"/></svg>Bettwäsche &amp;<br>Handtücher</div>
  </div>

</div>
</body>
</html>
```